Plavotok- plumbing service flyer

Hello,
We would like to create flyer for our plumbing company Plavotok
- we have 2 web domains
aquavelo-example.hr ( official)
preuredjenjedoma-example.hr ( for bathroom renovation)

- we would like to create a similar Z-fold flyer ( from A4 paper) for our services
- We are sending images used on our websites. Of Course, it is allowed to put some of their own. Depending on design
- sending word with text which should go on each page. Text can be modified but in the sense of a page. The massage on a page should be as in word.
What is important to us:
- to stay in blue color
- It should be 1 page when fully open. So it looks like the complete page of information
- first/front page should be with our logo and phone number. more focus on emergency plumbing.
- back page should be about bathroom remodeling. Not necessary but would be received more points
- please don't use images of regular plumbers from Pixelvault and similar. we don't want to use this stock's regular images as all others.

Target Market(s)

Bathroom remodeling and emergency plumbing

Industry/Entity Type

Construction-Plumbing

Colors
0054AA
0677BA
7BADD7
CADEEF
E8F1F8

Requirements
Must have
• Logo

```html
<!DOCTYPE html>
<html lang="en">
<head>
<meta charset="utf-8">
<title>Plavotok – Plumbing Service Z-Fold Flyer</title>
<link href="https://fonts.googleapis.com/css2?family=Anton&family=Oswald:wght@400;500&family=Montserrat:ital,wght@1,400&display=swap" rel="stylesheet">
<style>
:root{
  --stage:#fbb716;
  --navy:#1f3d86;
  --navy-deep:#152d68;
  --navy-light:#2b57aa;
  --panel-box:#1a3476;
  --gold:#f6b91b;
  --white:#ffffff;
  --red:#e3202a;
  --body:#e8f1f8;
}
*{margin:0;padding:0;box-sizing:border-box}
html,body{width:1200px;height:2242px;overflow:hidden;background:var(--stage)}
.stage{position:relative;width:1200px;height:2242px}

.spread{position:absolute;left:174px;width:856px;height:605px;overflow:hidden;
  background:linear-gradient(180deg,var(--navy) 0%,var(--navy-deep) 100%);
  box-shadow:0 26px 24px -16px rgba(120,70,0,.55)}
.spread--outside{top:850px}
.spread--inside{top:1557px;background:linear-gradient(180deg,var(--navy-light) 0%,var(--navy) 40%,var(--navy-deep) 100%)}

.header-photo{position:absolute;left:250px;top:0;width:606px;height:200px;
  background:linear-gradient(90deg,rgba(31,61,134,0),rgba(90,130,200,.28) 55%,rgba(31,61,134,.1))}
.swoosh{position:absolute;left:0;top:0;width:856px;height:605px}
.fold{position:absolute;top:0;left:572px;width:1px;height:605px;background:rgba(0,0,0,.2)}
.mascot-fade{position:absolute;border-radius:50%;
  background:radial-gradient(circle,rgba(90,140,220,.3),rgba(40,80,160,0) 70%)}

.brand{position:absolute;text-align:center}
.brand__mark{display:block;margin:0 auto;border-radius:50%;background:var(--navy-light);border:6px solid var(--gold)}
.brand__name{display:block;font-family:"Anton",sans-serif;line-height:1;color:var(--white);letter-spacing:1px}

.tagline{position:absolute;font:30px/1.12 "Anton",sans-serif;color:var(--gold)}
.tagline--name{color:var(--white);font-size:50px;line-height:1}

.contact-box{position:absolute;left:22px;width:238px;height:77px;display:flex;align-items:center;gap:12px;padding-left:14px}
.contact-box--quick{background:var(--panel-box)}
.contact-box--emergency{background:var(--red)}
.contact-box__label{font:500 16px/1.15 "Oswald",sans-serif;letter-spacing:3px;color:var(--white)}
.contact-box__sub{font:400 15px/1.2 "Oswald",sans-serif;color:var(--gold)}
.contact-box__small{font:500 12.5px/1.1 "Oswald",sans-serif;letter-spacing:2px;color:var(--white)}
.contact-box__phone{font:500 27px/1.05 "Oswald",sans-serif;color:var(--white)}

.heading{position:absolute;font:58px/0.92 "Anton",sans-serif;color:var(--white)}
.heading span{display:block;color:var(--gold)}
.heading--small{font-size:42px;line-height:1}

.body-copy{position:absolute;width:226px;font:italic 400 10px/11.9px "Montserrat",sans-serif;color:var(--body);text-align:justify}

.icon-row{position:absolute;left:592px;width:243px;border:1.5px solid var(--gold);border-radius:8px}
.service{position:absolute;width:110px;text-align:center}
.service__circle{width:87px;height:87px;margin:0 auto;border-radius:50%;border:1.5px solid var(--gold);
  background:var(--navy);display:flex;align-items:center;justify-content:center}
.service__label{margin-top:11px;font:12px/1 "Anton",sans-serif;color:var(--white);letter-spacing:.2px}
.service__circle-text{font:11.5px/1 "Anton",sans-serif;color:var(--white);text-align:center}

.emergency-line{position:absolute;left:22px;top:516px;display:flex;align-items:center;gap:12px}
.emergency-line .contact-box__small{font-size:14px;letter-spacing:2.6px}
.emergency-line .contact-box__phone{font-size:32px}
</style>
</head>
<body>
<main class="stage">

  <section class="spread spread--outside">
    <div class="header-photo" role="img" aria-label="Photograph of a plumber working on pipes, tinted blue"></div>
    <div class="mascot-fade" style="left:270px;top:376px;width:235px;height:229px" role="img" aria-label="Faint mascot illustration of the plumbing hero"></div>
    <div class="mascot-fade" style="left:583px;top:385px;width:269px;height:230px" role="img" aria-label="Faint mascot illustration holding a wrench"></div>
    <svg class="swoosh" viewBox="0 0 856 605" aria-hidden="true">
      <path d="M0 155 Q420 252 856 160 L856 156 Q420 238 0 151Z" fill="#f6b91b"/>
    </svg>
    <div class="fold"></div>

    <div class="brand" style="left:44px;top:44px;width:194px">
      <span class="brand__mark" style="width:120px;height:120px"></span>
      <span class="brand__name" style="font-size:40px;margin-top:12px">PLAVOTOK</span>
    </div>

    <p class="tagline" style="left:22px;top:266px;width:238px;text-align:center">USING TECH TO<br>FACILITATE YOUR LIFE.</p>
    <p class="tagline tagline--name" style="left:22px;top:337px;width:238px;text-align:center">PLAVOTOK</p>

    <div class="contact-box contact-box--quick" style="top:408px">
      <svg width="50" height="35" viewBox="0 0 64 46" aria-hidden="true">
        <g fill="none" stroke="#fff" stroke-width="3"><rect x="14" y="4" width="46" height="36"/><path d="M14 4 L37 24 L60 4M14 40 L32 22M60 40 L42 22"/><path d="M2 12h8M0 20h10M4 28h6"/></g>
      </svg>
      <div><p class="contact-box__label">QUICK CONTACT</p><p class="contact-box__sub">LEACKAGE / CLOGGED?</p></div>
    </div>
    <div class="contact-box contact-box--emergency" style="top:497px">
      <svg width="37" height="42" viewBox="0 0 52 56" aria-hidden="true">
        <g fill="none" stroke="#fff" stroke-width="3"><rect x="4" y="8" width="26" height="44" rx="4"/><circle cx="38" cy="14" r="11"/><path d="M12 24c2 8 6 12 12 14"/></g>
        <text x="38" y="18" font-size="11" fill="#fff" text-anchor="middle" font-family="Oswald,sans-serif">24</text>
      </svg>
      <div><p class="contact-box__small">EMERGENCY PLUMBING</p><p class="contact-box__phone">095-410-2287</p></div>
    </div>

    <h2 class="heading" style="left:316px;top:38px"><span>PLUMBING</span>SERVICE</h2>
    <h2 class="heading" style="left:588px;top:38px"><span>DRAIN</span>CLEANING</h2>

    <div class="body-copy" style="left:315px;top:222px">
      <p>Lorem Ipsum is simply dummy text of the printing and typesetting industry. Lorem Ipsum has been the industry's standard dummy text ever since the 1500s, when an unknown printer took a galley of type and scrambled it to make a type specimen book. It has survived not only five centuries, but also the leap into electronic typesetting.</p>
      <p>It was popularised in the 1960s with the release of Letraset sheets containing Lorem Ipsum passages, and more recently with desktop publishing software like Aldus PageMaker</p>
    </div>
    <div class="body-copy" style="left:580px;top:222px">
      <p>Lorem Ipsum is simply dummy text of the printing and typesetting industry. Lorem Ipsum has been the industry's standard dummy text ever since the 1500s, when an unknown printer took a galley of type and scrambled it to make a type specimen book. It has survived not only five centuries, but also the leap into electronic typesetting.</p>
      <p>It was popularised in the 1960s with the release of Letraset sheets containing Lorem Ipsum passages, and more recently with desktop publishing software like Aldus PageMaker</p>
      <p style="margin-top:12px">Lorem Ipsum is simply dummy text of the printing and typesetting industry. Lorem Ipsum has been the industry's standard dummy text ever since the 1500s, when an unknown printer took a galley</p>
    </div>
  </section>

  <section class="spread spread--inside">
    <div class="header-photo" style="left:0;width:856px" role="img" aria-label="Photograph of a plumbing team at work, tinted blue"></div>
    <div class="mascot-fade" style="left:322px;top:409px;width:235px;height:196px" role="img" aria-label="Faint mascot illustration of the plumbing hero"></div>
    <svg class="swoosh" viewBox="0 0 856 605" aria-hidden="true">
      <path d="M0 130 Q420 228 856 140 L856 136 Q420 214 0 126Z" fill="#f6b91b"/>
    </svg>

    <div class="brand" style="left:40px;top:34px;width:202px">
      <span class="brand__mark" style="width:130px;height:130px"></span>
      <span class="brand__name" style="font-size:44px;margin-top:12px">PLAVOTOK</span>
    </div>

    <p class="tagline" style="left:22px;top:284px;font-size:31px;line-height:0.92">COUNT ON US<br>FOR PLUMBING</p>
    <div class="body-copy" style="left:22px;top:354px;width:238px">
      <p>Lorem Ipsum is simply dummy text of the printing and typesetting industry. Lorem Ipsum has been the industry's standard dummy text ever since the 1500s, when an unknown printer took a galley of type and scrambled it to make a type specimen book. It has survived not only five centuries, but also the leap into electronic typesetting.</p>
    </div>

    <div class="emergency-line">
      <svg width="42" height="48" viewBox="0 0 52 56" aria-hidden="true">
        <g fill="none" stroke="#fff" stroke-width="3"><rect x="4" y="8" width="26" height="44" rx="4"/><circle cx="38" cy="14" r="11"/><path d="M12 24c2 8 6 12 12 14"/></g>
        <text x="38" y="18" font-size="11" fill="#fff" text-anchor="middle" font-family="Oswald,sans-serif">24</text>
      </svg>
      <div><p class="contact-box__small">EMERGENCY PLUMBING</p><p class="contact-box__phone">095-410-2287</p></div>
    </div>

    <h2 class="heading" style="left:316px;top:36px"><span>ROCKET</span>REWARDS</h2>
    <div class="body-copy" style="left:315px;top:209px">
      <p>Lorem Ipsum is simply dummy text of the printing and typesetting industry. Lorem Ipsum has been the industry's standard dummy text ever since the 1500s, when an unknown printer took a galley of type and scrambled it to make a type specimen book. It has survived not only five centuries, but also the leap into electronic typesetting.</p>
      <p>It was popularised in the 1960s with the release of Letraset sheets containing Lorem Ipsum passages, and more recently with desktop publishing software like Aldus PageMaker</p>
      <p style="margin-top:12px">It was popularised in the 1960s with the release of Letraset sheets containing Lorem Ipsum passages, and more recently with desktop publishing software like Aldus PageMaker</p>
    </div>

    <h2 class="heading heading--small" style="left:596px;top:34px"><span>COUNT ON US</span>FOR PLUMBING</h2>

    <div class="icon-row" style="top:220px;height:54px"></div>
    <div class="icon-row" style="top:344px;height:54px"></div>
    <div class="icon-row" style="top:471px;height:55px"></div>

    <div class="service" style="left:598px;top:202px">
      <div class="service__circle"><svg width="46" height="36" viewBox="0 0 60 46" aria-hidden="true"><path d="M20 10V4h20v6" fill="none" stroke="#fff" stroke-width="4"/><rect x="2" y="10" width="56" height="34" rx="4" fill="#fff"/><rect x="2" y="22" width="56" height="3" fill="#1f3d86"/></svg></div>
      <p class="service__label">REPAIRS</p>
    </div>
    <div class="service" style="left:720px;top:202px">
      <div class="service__circle"><svg width="46" height="46" viewBox="0 0 60 60" aria-hidden="true"><g fill="none" stroke="#fff"><circle cx="22" cy="22" r="12" stroke-width="8" stroke-dasharray="5 4"/><circle cx="42" cy="42" r="9" stroke-width="6" stroke-dasharray="4 3"/></g></svg></div>
      <p class="service__label">REPLACEMENTS</p>
    </div>
    <div class="service" style="left:598px;top:326px">
      <div class="service__circle"><p class="service__circle-text">CONTACT OUR<br>EXPERTS NOW</p></div>
      <p class="service__label">CONTACT</p>
    </div>
    <div class="service" style="left:720px;top:326px">
      <div class="service__circle"><svg width="42" height="46" viewBox="0 0 56 60" aria-hidden="true"><g fill="#fff"><path d="M8 22a16 16 0 0 1 32 0z"/><rect x="6" y="22" width="36" height="4"/><path d="M4 58c0-14 8-22 20-22s20 8 20 22z"/></g><path d="M48 6v40" stroke="#fff" stroke-width="6" stroke-linecap="round"/></svg></div>
      <p class="service__label">MAINTENANCE</p>
    </div>
    <div class="service" style="left:598px;top:454px">
      <div class="service__circle"><svg width="54" height="54" viewBox="0 0 70 70" aria-hidden="true"><path d="M60 35a25 25 0 1 1-8-18" fill="none" stroke="#fff" stroke-width="3"/><path d="M54 8v12H42" fill="none" stroke="#fff" stroke-width="3"/><text x="35" y="42" font-family="Anton,sans-serif" font-size="20" fill="#fff" text-anchor="middle">24/7</text></svg></div>
      <p class="service__label">24/7 EMERGENCY</p>
    </div>
    <div class="service" style="left:720px;top:454px">
      <div class="service__circle"><svg width="46" height="46" viewBox="0 0 60 60" aria-hidden="true"><path d="M12 12 L48 48" stroke="#fff" stroke-width="9" stroke-linecap="round"/><circle cx="12" cy="12" r="9" fill="none" stroke="#fff" stroke-width="5"/><path d="M48 12 L30 30" stroke="#fff" stroke-width="7" stroke-linecap="round"/></svg></div>
      <p class="service__label">INSTALLATIONS</p>
    </div>
  </section>

</main>
</body>
</html>
```